Health and Wellness company needs flyer to promote free seminar

Corvella Motion studio is a health and wellness company that offers an exercise program designed by physical therapists to help relieve pain and improve mobility. Our business is a new concept that is not well understood by the public. In order to promote our business we offer a free seminar where we present information regarding the underlying cause of pain and tightness. During the seminar we also perform a posture screen and movement testing for all participants.

Target Market(s)

Mostly healthy and active women ages 25-65

Industry/Entity Type

Health And Wellness

Font styles to use
Sans Serif

Colors

Designer to choose colors to be used in the design.

Requirements
Must have
• Title: Eliminate Pain and Tightness For Good
• Paragraph: Corvella Motion Studio offers a free 60 minute seminar: "The Busy Walker's Manual for Stretching and Living Lighter."
• What to Expect:
• • Identify the underlying cause of your pain and mobility issues
• • Expose what gets in the way of you moving and feeling better
• • Learn why traditional exercises don’t help and can actually make the problem worse
• • Reveal what your posture is saying and how that impacts you
• • Experience your muscle imbalances through movement tests
• • Discover the training method that realigns your posture, increases your mobility and reduces your pain
• Call to action: RSVP online at corvellamotionstudio.com
Nice to have
• Use a relevant image showing a female dealing with tightness in the low back, legs, etc.
• Emphasize that the seminar is FREE.
• Make the call to action prominent.

```html
<!DOCTYPE html>
<html lang="en">
<head>
<meta charset="utf-8">
<title>Corvella Motion Studio – Free Seminar</title>
<link href="https://fonts.googleapis.com/css2?family=Jost:wght@500;700&family=Zilla+Slab:wght@700&family=Open+Sans:wght@400;600;700&family=Arimo:wght@400;700&family=Montserrat:wght@700;800&display=swap" rel="stylesheet">
<style>
  :root {
    --navy: #25287e;
    --royal: #2f3396;
    --orange: #f7861a;
    --red: #e3231b;
    --grey: #c9c9c9;
    --white: #ffffff;
  }
  html, body { margin: 0; padding: 0; overflow: hidden; background: #ffffff; }
  .flyer {
    position: relative; width: 846px; height: 1200px; overflow: hidden;
    background: var(--white); font-family: "Open Sans", sans-serif;
  }
  .print-mark {
    position: absolute; top: 10px; right: 34px;
    font: 700 28px "Montserrat", sans-serif; color: var(--grey); letter-spacing: 1px;
  }
  .brand {
    position: absolute; top: 46px; left: 0; width: 846px;
    display: flex; justify-content: center; align-items: center; gap: 14px;
  }
  .brand-square { width: 40px; height: 40px; background: var(--orange); }
  .brand-name { font: 500 38px "Jost", sans-serif; color: var(--royal); }
  .title-band {
    position: absolute; left: 24px; top: 140px; width: 780px; height: 46px; margin: 0;
    background: var(--navy); color: var(--white);
    font: 700 35px/46px "Jost", sans-serif; text-align: center; letter-spacing: 0.5px;
  }
  .title-band .accent { color: var(--orange); }
  .shapes { position: absolute; inset: 0; }
  .badge {
    position: absolute; left: 35px; top: 266px; width: 240px; height: 152px;
    display: flex; flex-direction: column; align-items: center;
    transform: rotate(-8deg); text-align: center;
  }
  .badge .free { font: 800 64px/62px "Montserrat", sans-serif; color: var(--red); }
  .badge .minutes { font: 700 34px/42px "Open Sans", sans-serif; color: var(--white); }
  .badge .seminar { font: 700 40px/48px "Open Sans", sans-serif; color: var(--navy); letter-spacing: 1px; }
  .seminar-title {
    position: absolute; left: 26px; top: 514px; margin: 0;
    font: 700 26px/34px "Zilla Slab", serif; color: var(--white);
  }
  .seminar-title .line2 { padding-left: 16px; display: block; }
  .expect-heading {
    position: absolute; left: 26px; top: 606px; margin: 0;
    font: 700 19px "Arimo", sans-serif; color: var(--white);
  }
  .expect-list {
    position: absolute; left: 28px; top: 646px; width: 500px; margin: 0; padding: 0;
    list-style: none; color: var(--white); font-size: 15.5px; line-height: 17px;
  }
  .expect-list li { position: relative; padding-left: 14px; margin-bottom: 16px; }
  .expect-list li::before {
    content: ""; position: absolute; left: 1px; top: 5px; width: 3px; height: 6px;
    border: solid var(--orange); border-width: 0 2px 2px 0; transform: rotate(45deg);
  }
  .expect-list .verb { text-decoration: underline; }
  .rsvp {
    position: absolute; right: 46px; top: 1088px;
    font: 800 24px "Montserrat", sans-serif; color: var(--orange);
  }
  .url-band {
    position: absolute; left: 512px; top: 1124px; width: 334px; height: 52px;
    background: var(--navy); border-radius: 26px 0 0 26px;
    color: var(--white); font: 700 20px/52px "Montserrat", sans-serif; text-align: center;
  }
</style>
</head>
<body>
<div class="flyer">
  <div class="print-mark">CMYK</div>

  <div class="brand">
    <span class="brand-square"></span>
    <span class="brand-name">Corvella Motion Studio</span>
  </div>

  <h1 class="title-band">ELIMINATE PAIN &amp; <span class="accent">TIGHTNESS</span> FOR GOOD</h1>

  <svg class="shapes" width="846" height="1200" viewBox="0 0 846 1200">
    <defs>
      <linearGradient id="therapyTone" x1="0" y1="0" x2="1" y2="1">
        <stop offset="0" stop-color="#d9b8a6"/>
        <stop offset="0.45" stop-color="#5b2a5e"/>
        <stop offset="1" stop-color="#cfe8c8"/>
      </linearGradient>
      <linearGradient id="neckTone" x1="0" y1="0" x2="1" y2="1">
        <stop offset="0" stop-color="#8a6242"/>
        <stop offset="1" stop-color="#e9dcd2"/>
      </linearGradient>
      <linearGradient id="backTone" x1="0" y1="0" x2="0" y2="1">
        <stop offset="0" stop-color="#d9d9d9"/>
        <stop offset="0.5" stop-color="#c48a62"/>
        <stop offset="1" stop-color="#f29bc0"/>
      </linearGradient>
      <linearGradient id="kneeTone" x1="0" y1="0" x2="1" y2="1">
        <stop offset="0" stop-color="#c2332e"/>
        <stop offset="1" stop-color="#3a5f9a"/>
      </linearGradient>
      <clipPath id="clipNeck"><circle cx="112" cy="1012" r="106"/></clipPath>
      <clipPath id="clipBack"><circle cx="308" cy="1040" r="106"/></clipPath>
      <clipPath id="clipKnee"><circle cx="504" cy="992" r="114"/></clipPath>
    </defs>

    <path d="M0 452 Q200 425 420 398 T846 348 L846 1040 L0 1090 Z" fill="var(--royal)"/>

    <polygon class="burst" transform="translate(155 342)" fill="var(--orange)"
      points="150,0 121,16 145,39 113,47 130,75 97,74 106,106 74,97 75,130 47,113 39,145 16,121 0,150 -16,121 -39,145 -47,113 -75,130 -74,97 -106,106 -97,74 -130,75 -113,47 -145,39 -121,16 -150,0 -121,-16 -145,-39 -113,-47 -130,-75 -97,-74 -106,-106 -74,-97 -75,-130 -47,-113 -39,-145 -16,-121 0,-150 16,-121 39,-145 47,-113 75,-130 74,-97 106,-106 97,-74 130,-75 113,-47 145,-39 121,-16"/>

    <polygon points="540,235 846,235 846,850 560,900 540,880" fill="url(#therapyTone)" role="img" aria-label="Photo: therapist stretching a client's arm on a treatment table"/>

    <circle cx="112" cy="1012" r="110" fill="var(--royal)"/>
    <rect x="0" y="900" width="220" height="220" fill="url(#neckTone)" clip-path="url(#clipNeck)" role="img" aria-label="Photo: woman holding her sore neck"/>
    <circle cx="308" cy="1040" r="110" fill="var(--royal)"/>
    <rect x="200" y="930" width="220" height="220" fill="url(#backTone)" clip-path="url(#clipBack)" role="img" aria-label="Photo: woman holding her lower back"/>
    <circle cx="504" cy="992" r="118" fill="var(--royal)"/>
    <rect x="388" y="876" width="232" height="232" fill="url(#kneeTone)" clip-path="url(#clipKnee)" role="img" aria-label="Photo: woman on a sofa holding her sore knee"/>
  </svg>

  <div class="badge">
    <span class="free">FREE</span>
    <span class="minutes">60 minute</span>
    <span class="seminar">SEMINAR</span>
  </div>

  <h2 class="seminar-title">“The Busy Walker's Manual for<span class="line2">Stretching and Living Lighter”</span></h2>

  <h3 class="expect-heading">WHAT TO EXPECT</h3>
  <ul class="expect-list">
    <li><span class="verb">Identify</span> the underlying cause of your pain and mobility issues.</li>
    <li><span class="verb">Expose</span> what gets in the way of you moving and feeling better.</li>
    <li><span class="verb">Learn</span> why traditional exercises don’t help and can actually make the problem worse.</li>
    <li><span class="verb">Reveal</span> what your posture is saying and how that impacts you.</li>
    <li><span class="verb">Experience</span> your muscle imbalances through movement tests.</li>
    <li><span class="verb">Discover</span> the training method that realigns your posture, increases your mobility and reduces your pain.</li>
  </ul>

  <div class="rsvp">RSVP online at</div>
  <div class="url-band">corvellamotionstudio.com</div>
</div>
</body>
</html>
```